Stationery Design Project for Nimbora, Chicago

Nimbora, a street parking application which helps car drivers find a street parking spot by offering an ideal path along which to look for parking. This path is calculated by our algorithm based on data (e.g. historical data, baseball games schedule, etc.). Along this path the driver will find a spot and will also save 70% of the search time. Customer we target is reg. between 21 and 45 yo.

We envision something young, fresh, bright and original. Slightly abstract maybe. It should represent the idea and elements of finding street parking in the city, e.g. car(s), parking spot, people, city, etc. (just ideas!).

Logo is attached.

Requirement:
- Business Cards (2 Sided Full Color CMYK)
- Letterhead (1 Sided Full Color CMYK)
- Envelope (1 Sided Full Color CMYK)
- Sticker (1 Sided Full Color CMYK), round with a 2inch diameter.

Reason: We're starting to get more and more designs and need more time to look into all of them. Very exciting!! Thanks to everybody!

Hi all, we're in the process of selecting our favs. Though choices!!! Really good submissions. Will keep you posted and sorry for the delay.

Target Market(s)

Car drivers and owners between 21 and 45

Industry/Entity Type

Parking

Requirements
Must have
• Sticker should be round and include company URL nimbora.com and the new logo which we will attach soon.
Should not have
• Should not be too serious or boring.

```html
<!DOCTYPE html>
<html lang="en">
<head>
<meta charset="utf-8">
<title>Nimbora Business Card</title>
<link rel="stylesheet" href="https://fonts.googleapis.com/css2?family=Open+Sans:wght@400;600;700&display=swap">
<style>
  :root {
    --page-bg: #e4e4e4;
    --card-bg: #ffffff;
    --ink: #111111;
    --brand-blue: #1f3f9e;
    --brand-blue-light: #2f6fd6;
    --band-grey: #5f6063;
    --rule-grey: #6d6e70;
    --photo-dark: #4a4b4e;
    --photo-mid: #8d8f93;
    --font-body: "Open Sans", Arial, sans-serif;
  }
  * { margin: 0; padding: 0; box-sizing: border-box; }
  html, body { width: 956px; height: 1200px; overflow: hidden; }
  body {
    background: var(--page-bg);
    font-family: var(--font-body);
    color: var(--ink);
    position: relative;
  }
  .card {
    position: absolute;
    left: 74px;
    width: 798px;
    height: 456px;
    background: var(--card-bg);
    border-radius: 30px;
    overflow: hidden;
  }
  .card--front { top: 132px; }
  .card--back { top: 652px; }

  .brand { position: absolute; display: flex; align-items: center; }
  .brand__dot { border-radius: 50%; background: radial-gradient(circle at 40% 35%, var(--brand-blue-light), var(--brand-blue) 70%); flex: none; }
  .brand__name { font-weight: 600; color: var(--ink); letter-spacing: 1px; line-height: 1; }

  .card--front .brand { left: 52px; top: 38px; }
  .card--front .brand__dot { width: 146px; height: 146px; margin-right: 30px; }
  .card--front .brand__name { font-size: 86px; }

  .card--back .brand { left: 80px; top: 18px; }
  .card--back .brand__dot { width: 186px; height: 186px; margin-right: 30px; }
  .card--back .brand__name { font-size: 108px; }

  .name-band {
    position: absolute;
    left: 513px; top: 221px;
    width: 285px; height: 77px;
    display: flex;
  }
  .name-band__blue {
    width: 241px;
    background: linear-gradient(90deg, var(--brand-blue) 0%, var(--brand-blue-light) 55%, var(--brand-blue) 100%);
    color: #fff;
    padding: 7px 0 0 19px;
  }
  .name-band__grey { flex: 1; background: var(--band-grey); }
  .person-name { font-size: 24px; font-weight: 700; line-height: 30px; }
  .person-role { font-size: 18px; font-weight: 700; line-height: 24px; }

  .contact {
    position: absolute;
    left: 534px; top: 316px;
    list-style: none;
    font-size: 19px;
    line-height: 30px;
  }
  .contact li:nth-child(3) { margin-top: 0; }
  .contact b { font-weight: 700; }

  .address {
    position: absolute;
    left: 50px; top: 376px;
    font-size: 19px;
    line-height: 27px;
    font-style: normal;
  }

  .back-rule {
    position: absolute;
    left: 0; top: 241px;
    width: 100%; height: 5px;
    background: var(--rule-grey);
  }
  .back-photo {
    position: absolute;
    left: 0; top: 246px;
    width: 100%; height: 210px;
    background:
      radial-gradient(ellipse 120px 60px at 78% 30%, rgba(200,40,50,0.55), transparent),
      radial-gradient(ellipse 110px 50px at 85% 65%, rgba(30,40,110,0.55), transparent),
      linear-gradient(110deg, var(--photo-mid) 0%, var(--photo-dark) 45%, var(--photo-mid) 100%);
  }
</style>
</head>
<body>
  <section class="card card--front">
    <div class="brand">
      <span class="brand__dot"></span>
      <span class="brand__name">Nimbora</span>
    </div>
    <div class="name-band">
      <div class="name-band__blue">
        <p class="person-name">Your Name</p>
        <p class="person-role">Designation</p>
      </div>
      <div class="name-band__grey"></div>
    </div>
    <ul class="contact">
      <li><b>t</b> : 123-456-7890</li>
      <li><b>m</b> : 123-456-7890</li>
      <li><b>e</b> : name@website.com</li>
      <li style="line-height:26px"><b>w</b> : www.website.com</li>
    </ul>
    <address class="address">
      City Name, Street Name<br>
      State Name, Country Code
    </address>
  </section>

  <section class="card card--back">
    <div class="brand">
      <span class="brand__dot"></span>
      <span class="brand__name">Nimbora</span>
    </div>
    <div class="back-rule"></div>
    <div class="back-photo" role="img" aria-label="Photo of cars parked in marked street parking bays seen from above, with a cyclist passing on the road"></div>
  </section>
</body>
</html>
```